Counseling Practice Business Card

I need a professional looking business card incorporating my new logo that was just completed. Card needs to incorporate my name and title, description of my specialty, my address, my phone number, my fax number, my email and my website URL. I need to be able to choose design on/with different paper colors and textures.
I do not have a lot of business card ideas so I am open to anything but I want bold,sharp, clear card without additional designs other than my logo (see attached file info). I am open to different color backgrounds or paper colors including black. I do not like traditional brackets around area codes in phone number or dashes between numbers in phone number. Am open to other ways of presenting including periods between numbers as appropriate. I do not know enough to know what I like yet but I want card to coordinate and work together with my logo. My practice emphasizes natural mental health interventions so any use of color (with background paper color or the blue and green in my logo) that elicits nature is nice. In addition to black, any natural brown or wood looking background might be desirable also. Most of the offerings so far look very similar and boring.

Target Market(s)

Potential therapy clients and other professionals

Contact Information for Business Card

Card information:
Gerald M. Whitcombe, Ph.D.
Licensed Clinical Psychologist
Integrative Health Coach
4812 Marlowe Ridge Blvd SE
Suite 310
Duluth, GA 30096
(770) 415-2983 phone
(770) 581-4096 fax
drgeraldwhitcombe@quillmarsh.net
brightfernwellness.net

Font styles to use
Serif
Sans Serif
Other font styles liked:
• anything that you think looks crisp, clear and easily readable

Requirements
Must have
• Any color used should coordinate with my logo design (see attached files).
• Card should be printed horizontally so top and bottom are longest sides of rectangle.
• Background color or paper color should complement and highlight logo. Do not like a white background. black, grey, brown or any color my logo would blend well with.
Nice to have
• I would like designer to utilize color to highlight letters/name or phone-fax-web symbols.
• Bottom edge of card could be highlighted if appropriate to an idea.
Should not have
• I would NOT want the card to have a pure white background at all.
• No clear cards.
• Cards should be oriented with long sides on bottom and top, NOT sides. DO NOT LIKE THIS THIN TALL ORIENTATION.

```html
<!DOCTYPE html>
<html lang="en">
<head>
<meta charset="utf-8">
<title>Brightfern Wellness – Business Card</title>
<link rel="stylesheet" href="https://fonts.googleapis.com/css2?family=Roboto:wght@400;500;700&display=swap">
<style>
  :root {
    --backdrop: #3a3a3c;
    --card: #232427;
    --ink-light: #e9e9ea;
    --ink-soft: #c9cacc;
    --emboss: #6c6d70;
    --brand-blue: #2b78c4;
    --brand-green: #1f8a3c;
  }
  * { margin: 0; padding: 0; box-sizing: border-box; }
  html, body { width: 799px; height: 1200px; overflow: hidden; }
  body {
    background: var(--backdrop);
    font-family: "Roboto", Arial, sans-serif;
    position: relative;
  }
  .card {
    position: absolute;
    left: 80px;
    width: 640px;
    height: 366px;
    background: var(--card);
    border-radius: 3px;
    box-shadow: 0 14px 30px rgba(0,0,0,.45);
    overflow: hidden;
  }
  .card--front { top: 110px; }
  .card--back { top: 700px; }

  /* front */
  .front-mark {
    position: absolute;
    inset: 0;
    display: flex;
    align-items: center;
    justify-content: center;
    gap: 16px;
  }
  .front-mark__dot {
    width: 26px; height: 26px;
    border-radius: 50%;
    background: var(--emboss);
  }
  .front-mark__name {
    font-size: 44px;
    font-weight: 500;
    color: var(--emboss);
    letter-spacing: 1px;
  }

  /* back */
  .brand {
    position: absolute;
    left: 30px;
    top: 120px;
    display: flex;
    align-items: center;
    gap: 10px;
  }
  .brand__dot {
    width: 18px; height: 18px;
    border-radius: 50%;
    background: var(--brand-green);
  }
  .brand__name {
    font-size: 26px;
    font-weight: 500;
    color: var(--brand-blue);
  }
  .contact {
    position: absolute;
    left: 362px;
    top: 78px;
    right: 16px;
    color: var(--ink-light);
  }
  .contact__name {
    font-size: 19px;
    font-weight: 700;
    color: var(--brand-blue);
    white-space: nowrap;
  }
  .contact__title {
    font-size: 12px;
    line-height: 1.35;
    color: var(--ink-soft);
    margin-top: 3px;
  }
  .contact__address {
    font-size: 13.5px;
    line-height: 1.3;
    margin-top: 12px;
  }
  .contact__lines { list-style: none; margin-top: 8px; font-size: 13.5px; }
  .contact__lines li { display: flex; align-items: center; gap: 9px; line-height: 1.45; white-space: nowrap; }
  .contact__lines svg { width: 12px; height: 12px; fill: var(--brand-blue); flex: none; }

  .edge-green {
    position: absolute;
    left: 0; bottom: 0;
    width: 270px; height: 14px;
    background: var(--brand-green);
  }
  .edge-blue {
    position: absolute;
    left: 250px; right: 0; bottom: 0;
    height: 58px;
    background: var(--brand-blue);
    border-top-left-radius: 24px;
    display: flex;
    align-items: center;
    padding-left: 48px;
  }
  .edge-blue__url {
    color: #fff;
    font-size: 16px;
    letter-spacing: .3px;
  }
</style>
</head>
<body>

<section class="card card--front" aria-label="Card front">
  <div class="front-mark">
    <span class="front-mark__dot"></span>
    <span class="front-mark__name">Brightfern Wellness</span>
  </div>
</section>

<section class="card card--back" aria-label="Card back">
  <div class="brand">
    <span class="brand__dot"></span>
    <span class="brand__name">Brightfern Wellness</span>
  </div>

  <div class="contact">
    <p class="contact__name">Gerald M. Whitcombe, Ph.D.</p>
    <p class="contact__title">Licensed Clinical Psychologist<br>Integrative Health Coach</p>
    <p class="contact__address">4812 Marlowe Ridge Blvd SE, Suite 310<br>Duluth, GA 30096</p>
    <ul class="contact__lines">
      <li>
        <svg viewBox="0 0 24 24" aria-hidden="true"><path d="M6.6 10.8a15.1 15.1 0 0 0 6.6 6.6l2.2-2.2c.3-.3.7-.4 1-.2 1.1.4 2.3.6 3.6.6.6 0 1 .4 1 1V20c0 .6-.4 1-1 1A17 17 0 0 1 3 4c0-.6.4-1 1-1h3.5c.6 0 1 .4 1 1 0 1.3.2 2.5.6 3.6.1.3 0 .7-.2 1z"/></svg>
        770.415.2983
      </li>
      <li>
        <svg viewBox="0 0 24 24" aria-hidden="true"><path d="M6 2h10v6H6zM4 9h16a2 2 0 0 1 2 2v7h-4v4H6v-4H2v-7a2 2 0 0 1 2-2zm4 8v3h8v-3z"/></svg>
        770.581.4096
      </li>
      <li>
        <svg viewBox="0 0 24 24" aria-hidden="true"><path d="M2 5h20v14H2zm2 2v.5l8 5 8-5V7z"/></svg>
        drgeraldwhitcombe@quillmarsh.net
      </li>
    </ul>
  </div>

  <div class="edge-green"></div>
  <div class="edge-blue"><span class="edge-blue__url">www.brightfernwellness.net</span></div>
</section>

</body>
</html>
```